Novexa company website, a website for employment for people with autism

The website will make a match between people and jobs, mainly in the graphical sector, but also other sectors.
The name of the company is novexa and automates jobs with people that are on the autism spectrum.
The whole matchmaking and feedback process and so doesn't have to be in this prototype, we just want the general information pages and to convey a great look and brand identity that we will keep in the other pages to be developed. The website must be made with Wordpress, since the backend will be developed in Wordpress too.
It is a social project that wants to create possibilites for people with ASS to work from home for an employer or to do a variety of tasks for different customers.
The people we hire are generally not on the regular job market or have difficulty finding a job and "selling themselves"

Target Market(s)

matchmaking between talent (with ASS) and employers / jobs

Number of Pages Required

5+ page

Font styles to use
Sans Serif

Colors
ec1f27
e34298
a64599
6b449b
0355a3
0792cd

Requirements
Must have
• A stunning landing pages
• Integrate our logo and must match with what will do. We want a clean, modern, minimalistic, sleek website that radiates creativity and good looks.
• We have one page describing what we can do for customers, one page for people with ASS that would like to be candidates (our approach, learning program, ...), two pages that are addressed to partners who want to cooperate: the one's that can assist with autism related assistance and the one's that can help with the job coaching.
Nice to have
• In our logo are many colors as we embrace diversity and want to show that. Out main branding colors are red (for action) and blue for stability and will all gradients that go with it. Mainly white or black (or anthracite) for other parts
Should not have
• We want a modern and minimalistic design, no fluffy designs with lots of ornaments.

```html
<!DOCTYPE html>
<html lang="en">
<head>
<meta charset="utf-8">
<title>Novexa – Jobs for people on the autism spectrum</title>
<link href="https://fonts.googleapis.com/css2?family=Poppins:wght@400;500;600;700&family=Roboto:wght@300;400;500;700&display=swap" rel="stylesheet">
<style>
:root{
  --red:#ec1f27;--pink:#e34298;--purple:#a64599;--violet:#6b449b;--blue:#0355a3;--sky:#0792cd;
  --band:#2b8fd6;--ink:#1d1d1d;--text:#555;--muted:#888;--line:#e3e3e3;--grey:#f2f2f2;--black:#0d0d0d;--white:#fff;
}
*{box-sizing:border-box;margin:0;padding:0}
html,body{width:1200px;height:4018px;overflow:hidden}
body{font-family:"Roboto",sans-serif;color:var(--ink);background:var(--white);position:relative}
.abs{position:absolute}
.stripe{position:absolute;left:0;width:1200px;height:7px;background:linear-gradient(90deg,var(--red) 0 16%,var(--pink) 16% 32%,var(--purple) 32% 48%,var(--violet) 48% 64%,var(--blue) 64% 82%,var(--sky) 82%)}
/* header */
.header{position:absolute;top:0;left:0;width:1200px;height:128px}
.brand{position:absolute;left:148px;top:30px;display:flex;align-items:center;gap:14px}
.brand-mark{width:34px;height:34px;background:var(--blue)}
.brand-name{font-family:"Poppins",sans-serif;font-weight:600;font-size:34px;letter-spacing:3px;color:var(--ink)}
.call{position:absolute;left:533px;top:20px;display:flex;align-items:center;gap:12px}
.call-icon{width:38px;height:38px;border-radius:50%;background:var(--blue);display:flex;align-items:center;justify-content:center}
.call small{display:block;font-size:17px;color:var(--ink)}
.call strong{display:block;font-size:25px;font-weight:500;line-height:1}
.btn-outline{position:absolute;top:23px;height:36px;border-radius:18px;border:2px solid;font-size:14px;font-weight:500;display:flex;align-items:center;justify-content:center;gap:6px}
.btn-login{left:772px;width:126px;border-color:var(--sky);color:var(--sky)}
.btn-register{left:912px;width:142px;border-color:var(--pink);color:var(--pink)}
.nav{position:absolute;top:86px;left:442px;display:flex;gap:30px;font-size:16px;font-weight:500;text-transform:uppercase;color:#222}
/* hero */
.hero{position:absolute;top:134px;left:0;width:1200px;height:616px;background:radial-gradient(ellipse at 40% 35%,#3a2a6a 0,#1b1c40 30%,#07070f 70%)}
.play{position:absolute;left:568px;top:278px;width:66px;height:66px;border-radius:50%;background:#fff;display:flex;align-items:center;justify-content:center}
/* search band */
.search{position:absolute;top:750px;left:0;width:1200px;height:148px;background:var(--band)}
.search::before{content:"";position:absolute;left:588px;top:-12px;border:12px solid transparent;border-top:0;border-bottom-color:var(--band)}
.search h2{position:absolute;top:24px;width:100%;text-align:center;font-family:"Poppins",sans-serif;font-weight:600;font-size:28px;color:#fff;letter-spacing:1px}
.select{position:absolute;top:76px;height:40px;background:#fff;font-size:12px;color:#555;padding:0 12px;display:flex;align-items:center;justify-content:space-between}
.select::after{content:"";border:5px solid transparent;border-top:6px solid #333;margin-top:5px}
.go{position:absolute;top:76px;left:820px;width:206px;height:40px;background:var(--red);color:#fff;font-weight:700;font-size:17px;display:flex;align-items:center;justify-content:center;gap:6px}
/* features */
.section-title{position:absolute;width:1200px;text-align:center;font-family:"Poppins",sans-serif;font-weight:600;color:var(--ink)}
.section-sub{position:absolute;width:1200px;text-align:center;font-size:19px;color:#333}
.feature{position:absolute;top:1117px;width:286px;height:176px;border:1px solid var(--line);box-shadow:0 2px 6px rgba(0,0,0,.05);padding:28px 18px}
.feature svg{position:absolute;left:18px;top:28px}
.feature h3{margin-left:66px;font-family:"Poppins",sans-serif;font-weight:500;font-size:16px;color:#222}
.feature p{margin-left:66px;margin-top:12px;font-size:13px;line-height:19px;color:var(--muted)}
.feature a{display:block;margin-left:66px;margin-top:10px;font-size:13px;color:var(--blue);font-weight:500}
/* welcome */
.welcome-art{position:absolute;left:139px;top:1390px;width:312px;height:304px;display:flex;align-items:center;justify-content:center;gap:14px;background:linear-gradient(135deg,#f5f5f7,#e8e8ee)}
.welcome-art span{font-family:"Poppins",sans-serif;font-weight:600;font-size:34px;color:var(--ink)}
.welcome-art i{width:34px;height:34px;background:var(--purple)}
.divider{position:absolute;left:490px;top:1390px;width:1px;height:300px;background:var(--line)}
.welcome h2{position:absolute;left:536px;top:1384px;font-size:40px;font-weight:500}
.welcome h2 span{font-weight:300}
.welcome p{position:absolute;left:536px;top:1456px;width:520px;font-size:14px;line-height:31px;color:#555}
.read-more{position:absolute;left:536px;top:1634px;width:144px;height:42px;border:2px solid #222;border-radius:21px;font-weight:500;font-size:15px;display:flex;align-items:center;justify-content:center}
/* jobs */
.jobs-bg{position:absolute;top:1809px;left:0;width:1200px;height:999px;background:var(--grey)}
.jobs-band{position:absolute;top:1809px;left:0;width:1200px;height:375px;background:linear-gradient(100deg,#0a8fd1,#1aa4dc 50%,#0a86c8)}
.jobs-title{top:1892px;font-size:36px;color:#fff;font-weight:600}
.job{position:absolute;width:287px;height:326px;background:#fff;box-shadow:0 3px 10px rgba(0,0,0,.12);text-align:center}
.job .photo{height:174px}
.job .dot{position:absolute;left:122px;top:152px;width:44px;height:44px;border-radius:50%;background:#fff;display:flex;align-items:center;justify-content:center}
.job .dot::after{content:"";width:24px;height:24px;border-radius:50%;background:var(--purple)}
.job h3{margin-top:44px;font-family:"Poppins",sans-serif;font-weight:600;font-size:16px;color:#222}
.job p{margin:14px auto 0;width:240px;font-size:13px;line-height:22px;color:#666}
/* testimonials */
.clients-title{top:2888px;font-size:38px;color:#222;font-weight:600}
.quote{position:absolute;top:2990px;width:300px}
.quote .mark{position:absolute;left:0;top:0;font-family:"Poppins",sans-serif;font-size:38px;line-height:30px;color:#aaa}
.quote p{margin-left:36px;font-size:13px;line-height:21px;color:#555}
.quote .avatar{position:absolute;left:0;top:118px;width:76px;height:76px;border-radius:50%;background:linear-gradient(135deg,#c8ccd4,#8a8f9a)}
.quote .who{position:absolute;left:94px;top:124px}
.who b{display:block;color:var(--sky);font-weight:500;font-size:15px}
.who small{display:block;font-size:14px;color:#444;margin-top:4px}
.who .stars{color:var(--red);font-size:14px;letter-spacing:3px;margin-top:4px}
.arrow{position:absolute;top:3061px;width:28px;height:28px;border-radius:50%;background:#999;display:flex;align-items:center;justify-content:center}
/* partners */
.partners{position:absolute;top:3323px;left:0;width:1200px;height:188px;background:#f4f4f4;border-top:1px solid #ddd;display:flex;align-items:center;justify-content:center;gap:64px;font-family:"Poppins",sans-serif;font-weight:600;font-size:26px;color:#8d8d8d}
/* footer */
.footer{position:absolute;top:3517px;left:0;width:1200px;height:409px;background:var(--black);color:#ddd}
.footer h4{position:absolute;top:82px;font-family:"Poppins",sans-serif;font-weight:600;font-size:23px;color:#fff}
.contact-line{position:absolute;left:142px;display:flex;gap:14px;font-size:14px;line-height:20px}
.links{position:absolute;left:442px;top:136px;list-style:none;font-size:14px;line-height:27px}
.links li::before{content:"";display:inline-block;width:9px;height:9px;border-radius:50%;background:#fff;margin-right:14px}
.news-sub{position:absolute;left:670px;top:140px;font-size:14px}
.email{position:absolute;left:670px;top:178px;width:258px;height:38px;background:#fff;color:#888;font-size:11px;padding:12px 10px}
.subscribe{position:absolute;left:940px;top:178px;width:114px;height:38px;background:var(--blue);color:#fff;font-size:12px;font-weight:700;display:flex;align-items:center;justify-content:center}
.hours{position:absolute;left:670px;top:242px;font-size:13px;line-height:21px}
.hours b{display:block;font-size:14px;color:#fff;margin-bottom:4px}
.social{position:absolute;left:880px;top:270px;display:flex;gap:8px}
.social span{width:32px;height:32px;border-radius:50%;border:2px solid #fff}
.bottom{position:absolute;top:3926px;left:0;width:1200px;height:92px;background:var(--black);border-top:1px solid #2a2a2a;text-align:center;font-size:15px;color:#ddd;padding-top:34px}
</style>
</head>
<body>

<header class="header">
  <div class="brand"><span class="brand-mark"></span><span class="brand-name">NOVEXA</span></div>
  <div class="call">
    <span class="call-icon"><svg width="18" height="18" viewBox="0 0 24 24"><path fill="#fff" d="M6.6 10.8a15 15 0 006.6 6.6l2.2-2.2a1 1 0 011-.25 11 11 0 003.6.6 1 1 0 011 1V20a1 1 0 01-1 1A17 17 0 013 4a1 1 0 011-1h3.5a1 1 0 011 1 11 11 0 00.6 3.6 1 1 0 01-.25 1z"/></svg></span>
    <div><small>Call Us :</small><strong>555-014-2290</strong></div>
  </div>
  <a class="btn-outline btn-login"><svg width="14" height="14" viewBox="0 0 24 24" fill="none" stroke="currentColor" stroke-width="2"><circle cx="12" cy="8" r="4"/><path d="M4 21c0-4 4-6 8-6s8 2 8 6"/></svg>LOGIN</a>
  <a class="btn-outline btn-register"><svg width="14" height="14" viewBox="0 0 24 24" fill="none" stroke="currentColor" stroke-width="2"><path d="M4 20h4l10-10-4-4L4 16z"/></svg>REGISTER</a>
  <nav class="nav"><span>Home</span><span>Jobs</span><span>Services</span><span>Candidates</span><span>Employers</span><span>Blog</span><span>Contact</span></nav>
</header>
<div class="stripe" style="top:127px"></div>

<section class="hero" role="img" aria-label="Video still: abstract blue and red glowing smoke on a dark background">
  <div class="play"><svg width="26" height="28" viewBox="0 0 26 28"><path d="M4 2l20 12L4 26z" fill="#111"/></svg></div>
</section>

<section class="search">
  <h2>FINDING A JOB</h2>
  <div class="select" style="left:174px;width:204px">Type address</div>
  <div class="select" style="left:389px;width:203px">Email address</div>
  <div class="select" style="left:606px;width:203px">Automates jobs</div>
  <div class="go">GET STARTED <svg width="15" height="15" viewBox="0 0 24 24" fill="none" stroke="#fff" stroke-width="2.5"><circle cx="12" cy="12" r="10"/><path d="M10 8l4 4-4 4"/></svg></div>
</section>

<h2 class="section-title" style="top:982px;font-size:29px;font-weight:500">All The Jobs You Want In One Simple Place</h2>
<p class="section-sub" style="top:1038px">Find the jobs you want in just a few simple quick</p>

<article class="feature" style="left:145px">
  <svg width="48" height="36" viewBox="0 0 48 36"><rect x="2" y="4" width="44" height="28" rx="3" fill="none" stroke="var(--blue)" stroke-width="3"/><circle cx="14" cy="15" r="4" fill="var(--blue)"/><path d="M8 26c0-4 3-5 6-5s6 1 6 5z" fill="var(--blue)"/><path d="M26 13h14M26 19h14M26 25h10" stroke="var(--blue)" stroke-width="3"/></svg>
  <h3>Free Membership</h3>
  <p>Sed ut perspiciatis unde omnis iste natus error sit voluptatem accusium doloremque</p>
  <a>Read More ⊙</a>
</article>
<article class="feature" style="left:453px">
  <svg width="48" height="48" viewBox="0 0 48 48" fill="none" stroke="var(--blue)" stroke-width="3"><circle cx="24" cy="24" r="20"/><ellipse cx="24" cy="24" rx="9" ry="20"/><path d="M4 24h40M8 13h32M8 35h32"/></svg>
  <h3>Build resume Online</h3>
  <p>Sed ut perspiciatis unde omnis iste natus error sit voluptatem accusium doloremque</p>
  <a>Read More ⊙</a>
</article>
<article class="feature" style="left:764px;width:292px">
  <svg width="48" height="36" viewBox="0 0 48 36" fill="none" stroke="var(--blue)" stroke-width="3"><rect x="2" y="3" width="44" height="30" rx="3"/><path d="M3 5l21 16L45 5"/></svg>
  <h3>Job Suggestions</h3>
  <p>Sed ut perspiciatis unde omnis iste natus error sit voluptatem accusium doloremque</p>
  <a>Read More ⊙</a>
</article>

<section class="welcome">
  <div class="welcome-art" role="img" aria-label="Novexa brand emblem"><i></i><span>Novexa</span></div>
  <div class="divider"></div>
  <h2>Welcome to <span>Novexa</span></h2>
  <p>Sed ut perspiciatis unde omnis iste natus error sit voluptatem accusantium doloremque laudantium, totam rem aperiam, eaque ipsa quae ab illo inventore veritatis et quasi architecto beatae vitae dicta sunt explicabo. Nem enim ipsam voluptatem quia voluptas sit aspernatur aut odit aut fugit, sed quia consequuntur magni dolores eos qui ratione voluptatem sequi nesciunt. vitae dicta</p>
  <a class="read-more">READ MORE</a>
</section>

<div class="jobs-bg"></div>
<div class="jobs-band"></div>
<h2 class="section-title jobs-title">AUTOMATES JOBS</h2>

<article class="job" style="left:145px;top:2010px"><div class="photo" role="img" aria-label="Photo: two colleagues working together at a desk" style="background:linear-gradient(135deg,#8a7a6a,#3b3433)"></div><span class="dot"></span><h3>QUIS AUTEM VEL EUM IURE</h3><p>Sed ut perspiciatis unde omnis iste natus error sit voluptatem</p></article>
<article class="job" style="left:456px;top:2010px"><div class="photo" role="img" aria-label="Photo: smiling young woman at a computer in an office" style="background:linear-gradient(135deg,#5a5048,#1f1c1c)"></div><span class="dot"></span><h3>QUIS AUTEM VEL EUM IURE</h3><p>Sed ut perspiciatis unde omnis iste natus error sit voluptatem</p></article>
<article class="job" style="left:766px;top:2010px"><div class="photo" role="img" aria-label="Photo: young man preparing food in a kitchen" style="background:linear-gradient(135deg,#b7aa9a,#5a4a3e)"></div><span class="dot"></span><h3>QUIS AUTEM VEL EUM IURE</h3><p>Sed ut perspiciatis unde omnis iste natus error sit voluptatem</p></article>
<article class="job" style="left:145px;top:2362px"><div class="photo" role="img" aria-label="Photo: cheerful man giving a thumbs up at a laptop" style="background:linear-gradient(135deg,#5f6a3e,#2c2f22)"></div><span class="dot"></span><h3>QUIS AUTEM VEL EUM IURE</h3><p>Sed ut perspiciatis unde omnis iste natus error sit voluptatem</p></article>
<article class="job" style="left:456px;top:2362px"><div class="photo" role="img" aria-label="Photo: businessman in a suit at his desk" style="background:linear-gradient(135deg,#3e3a38,#121212)"></div><span class="dot"></span><h3>QUIS AUTEM VEL EUM IURE</h3><p>Sed ut perspiciatis unde omnis iste natus error sit voluptatem</p></article>
<article class="job" style="left:766px;top:2362px"><div class="photo" role="img" aria-label="Photo: workers handling goods in a workshop" style="background:linear-gradient(135deg,#7a4a3e,#3a2624)"></div><span class="dot"></span><h3>QUIS AUTEM VEL EUM IURE</h3><p>Sed ut perspiciatis unde omnis iste natus error sit voluptatem</p></article>

<h2 class="section-title clients-title">OUR CLIENTS SAYS</h2>
<span class="arrow" style="left:77px"><svg width="10" height="12" viewBox="0 0 10 12"><path d="M7 1L2 6l5 5" stroke="#fff" stroke-width="2" fill="none"/></svg></span>
<span class="arrow" style="left:1095px"><svg width="10" height="12" viewBox="0 0 10 12"><path d="M3 1l5 5-5 5" stroke="#fff" stroke-width="2" fill="none"/></svg></span>

<blockquote class="quote" style="left:142px"><span class="mark">❝</span><p>Sed ut perspiciatis unde omnis iste natus error sit voluptatem accusantium doloremque laudantium, totam rem aperiam, eaque ipsa quae ab illo inventore</p><span class="avatar" role="img" aria-label="Client portrait"></span><div class="who"><b>Lena T Marsh</b><small>novexa</small><div class="stars">★★★★★</div></div></blockquote>
<blockquote class="quote" style="left:466px"><span class="mark">❝</span><p>Sed ut perspiciatis unde omnis iste natus error sit voluptatem accusantium doloremque laudantium, totam rem aperiam, eaque ipsa quae ab illo inventore</p><span class="avatar" role="img" aria-label="Client portrait"></span><div class="who"><b>Lena T Marsh</b><small>novexa</small><div class="stars">★★★★★</div></div></blockquote>
<blockquote class="quote" style="left:793px"><span class="mark">❝</span><p>Sed ut perspiciatis unde omnis iste natus error sit voluptatem accusantium doloremque laudantium, totam rem aperiam, eaque ipsa quae ab illo inventore</p><span class="avatar" role="img" aria-label="Client portrait"></span><div class="who"><b>Lena T Marsh</b><small>novexa</small><div class="stars">★★★★★</div></div></blockquote>

<section class="partners"><span>SWIFTA</span><span>Corvana</span><span>MERIDOX</span><span>Talvex</span><span>leafy</span><span>BRONTIQ</span></section>
<div class="stripe" style="top:3510px"></div>

<footer class="footer">
  <h4 style="left:142px">CONTACT US</h4>
  <div class="contact-line" style="top:136px"><svg width="14" height="20" viewBox="0 0 14 20"><path d="M7 1a6 6 0 016 6c0 5-6 12-6 12S1 12 1 7a6 6 0 016-6z" fill="none" stroke="#fff" stroke-width="1.6"/><circle cx="7" cy="7" r="2" fill="#fff"/></svg><span>Novexa<br>autism spectrum<br>1180 Lindenfeld Austria</span></div>
  <div class="contact-line" style="top:212px"><svg width="16" height="16" viewBox="0 0 24 24"><path fill="none" stroke="#fff" stroke-width="2" d="M6.6 10.8a15 15 0 006.6 6.6l2.2-2.2 4.6 1.6V20A17 17 0 013 4h3.5l1.6 4.6z"/></svg><span>Phone: +43 (0) 5550 1420-0</span></div>
  <div class="contact-line" style="top:250px"><svg width="16" height="16" viewBox="0 0 16 16"><rect x="1" y="5" width="14" height="8" fill="#fff"/><rect x="4" y="1" width="8" height="5" fill="none" stroke="#fff" stroke-width="1.5"/></svg><span>Fax: +43 (0) 5550 1477</span></div>
  <div class="contact-line" style="top:286px"><svg width="16" height="12" viewBox="0 0 16 12"><rect x="1" y="1" width="14" height="10" fill="none" stroke="#fff" stroke-width="1.5"/><path d="M1 1l7 6 7-6" fill="none" stroke="#fff" stroke-width="1.5"/></svg><span>E-Mail: office@novexa.com</span></div>

  <h4 style="left:442px">QUICK LINKS</h4>
  <ul class="links"><li>Home</li><li>Jobs</li><li>Services</li><li>Candidates</li><li>Employers</li><li>Blog</li><li>Contact</li></ul>

  <h4 style="left:670px">SIGN UP FOR NEWSLETTER</h4>
  <p class="news-sub">Sign up to our mailing list</p>
  <div class="email">Enter email</div>
  <div class="subscribe">SUBSCRIPTION</div>
  <div class="hours"><b>OFFICE HOURS</b>Mon.-thu. 07:30 - 12:00<br>Mon.-thu. 12:30 - 16:30<br>Fri. 07:30 - 12:30</div>
  <div class="social"><span></span><span></span><span></span><span></span></div>
</footer>
<div class="bottom">(c) 2019 Novexa | All Rights Reserved | Disclaimer</div>

</body>
</html>
```